Heritage Hollow Business Cards

Require a business card design. <br/><br/>Needs to include logo (either round or long version) plus these details:<br/>Maya Torvell<br/>Heritage Hollow<br/>maya@kelvadtrading.com.au<br/>02 6481 7395<br/>PO Box Glenwarra NSW 2791<br/>www.heritagehollow.com.au<br/><br/>I need in an editable format so that I can create for multiple staff members. <br/><br/>

Target Market(s)

We are an online store selling renovation products to home owners are builders. Looking for a classic classy design.

Industry/Entity Type

Home And Garden

Contact Information for Business Card

Maya Torvell
Heritage Hollow
maya@kelvadtrading.com.au
02 6481 7395
PO Box Glenwarra NSW 2791
www.heritagehollow.com.au

Colors

Designer to choose colors to be used in the design.

Requirements
Must have
• Must include Logo.

```html
<!DOCTYPE html>
<html lang="en">
<head>
<meta charset="utf-8">
<title>Heritage Hollow Business Cards</title>
<link href="https://fonts.googleapis.com/css2?family=Work+Sans:wght@400;500;700&display=swap" rel="stylesheet">
<style>
  :root {
    --backdrop: #dcdcdc;
    --card-dark: #1c1c1c;
    --card-dark-edge: #2a2a2a;
    --card-light: #ffffff;
    --ink: #161616;
    --ink-soft: #6b6b6b;
    --on-dark: #f2f2f2;
    --rule: #1a1a1a;
  }
  * { box-sizing: border-box; margin: 0; padding: 0; }
  html, body {
    width: 1200px; height: 900px; overflow: hidden;
    background: var(--backdrop);
    font-family: "Work Sans", Arial, sans-serif;
  }
  .canvas {
    width: 1200px; height: 900px;
    display: flex; flex-direction: column; align-items: center; justify-content: center;
    gap: 48px;
  }
  .card {
    width: 600px; height: 366px; position: relative;
    box-shadow: 0 8px 22px rgba(0,0,0,0.25);
  }
  /* back of card */
  .card--back {
    background: radial-gradient(circle at 65% 30%, var(--card-dark-edge), var(--card-dark) 70%);
    color: var(--on-dark);
    display: flex; flex-direction: column; align-items: center; justify-content: center;
  }
  .brand-mark {
    width: 200px; height: 200px; border-radius: 50%;
    display: flex; align-items: center; justify-content: center;
    text-align: center;
    font-weight: 500; font-size: 30px; line-height: 1.05;
  }
  .card--back .brand-mark { border: 1px solid var(--on-dark); color: var(--on-dark); }
  .back-url {
    margin-top: 26px;
    font-size: 15px; letter-spacing: 4px; font-weight: 400;
  }
  /* front of card */
  .card--front {
    background: var(--card-light); color: var(--ink);
    display: flex; align-items: center;
  }
  .card--front .brand-mark {
    border: 1px solid var(--ink); color: var(--ink);
    margin-left: 44px; flex: none;
  }
  .divider {
    width: 1.5px; height: 200px; background: var(--rule);
    margin: 0 30px 0 40px; flex: none;
  }
  .details { display: flex; flex-direction: column; }
  .person-name { font-size: 30px; font-weight: 700; letter-spacing: 1.5px; }
  .person-role { font-size: 14px; color: var(--ink-soft); margin-top: 2px; letter-spacing: 0.5px; }
  .company { font-size: 16px; margin-top: 12px; }
  .address { font-size: 16px; color: var(--ink-soft); margin-top: 4px; line-height: 1.3; letter-spacing: 0.6px; }
  .contacts { list-style: none; margin-top: 10px; }
  .contact {
    display: flex; align-items: center; gap: 10px;
    font-size: 16px; color: var(--ink-soft); line-height: 1.45; letter-spacing: 0.4px;
  }
  .contact svg { width: 13px; height: 13px; flex: none; }
</style>
</head>
<body>
<main class="canvas">
  <section class="card card--back">
    <div class="brand-mark">Heritage<br>Hollow</div>
    <p class="back-url">www.heritagehollow.com.au</p>
  </section>

  <section class="card card--front">
    <div class="brand-mark">Heritage<br>Hollow</div>
    <div class="divider"></div>
    <div class="details">
      <h1 class="person-name">Maya Torvell</h1>
      <p class="person-role">Director</p>
      <p class="company">Heritage Hollow</p>
      <p class="address">PO Box Glenwarra<br>NSW 2791</p>
      <ul class="contacts">
        <li class="contact">
          <svg viewBox="0 0 16 16" aria-hidden="true"><path d="M4 1.5l2.2 3-1.3 1.6c.9 2 2.4 3.6 4.4 4.6l1.6-1.3 3 2.2-1.2 2.4c-5.6-.6-10-5-10.6-10.6z" fill="#333"/></svg>
          02 6481 7395
        </li>
        <li class="contact">
          <svg viewBox="0 0 16 16" aria-hidden="true"><rect x="1.5" y="3.5" width="13" height="9" fill="none" stroke="#333" stroke-width="1.4"/><path d="M1.5 3.5L8 9l6.5-5.5" fill="none" stroke="#333" stroke-width="1.4"/></svg>
          maya@kelvadtrading.com.au
        </li>
        <li class="contact">
          <svg viewBox="0 0 16 16" aria-hidden="true"><circle cx="8" cy="8" r="6.5" fill="none" stroke="#333" stroke-width="1.3"/><ellipse cx="8" cy="8" rx="3" ry="6.5" fill="none" stroke="#333" stroke-width="1.1"/><path d="M1.5 8h13" stroke="#333" stroke-width="1.1"/></svg>
          www.heritagehollow.com.au
        </li>
      </ul>
    </div>
  </section>
</main>
</body>
</html>
```